Casino with the 'highest winning percentage' needs a stationery design

This is for a casino in Colombo, Sri Lanka and we need a stationery design for business card, letter head and envelope.

Should be very professional, simple and elegant without fancy fonts

Reason: Not fully satisfied with the designs. Need more designs.

Business

• 1. card deck symbol 'CLUBS' in red, or black

2. name in BLOCK CAPITAL LETTERS

3. Preferred font colours are black, white or red

4. Prefer 'professional /elegant' fonts
• SHOULD NOT HAVE ANY OTHER SYMBOL EXCEPT 'CLUBS'

DO NOT PREFER ITALIC FONTS

```html
<!DOCTYPE html>
<html lang="en">
<head>
<meta charset="utf-8">
<title>Corvan Entertainment – Stationery</title>
<link rel="stylesheet" href="https://fonts.googleapis.com/css2?family=PT+Serif:wght@400;700&family=Jost:wght@300;400&display=swap">
<style>
  :root {
    --backdrop: #e7e4df;
    --paper-top: #ffffff;
    --paper-bottom: #e9e9ea;
    --ink: #1b1b1b;
    --ink-soft: #3a3a3a;
    --rule: #555555;
    --brand-red: #d42f3a;
    --suit-faint: #f1dada;
    --suit-grey: #dcdcdc;
    --tab-black: #111111;
    --label: #ffffff;
  }
  * { margin: 0; padding: 0; box-sizing: border-box; }
  html, body { width: 1200px; height: 387px; overflow: hidden; }
  body {
    background: var(--backdrop);
    font-family: "PT Serif", Georgia, serif;
    color: var(--ink);
    position: relative;
  }
  .sheet, .envelope, .envelope-back, .envelope-middle, .card {
    position: absolute;
    background: linear-gradient(160deg, var(--paper-top) 30%, var(--paper-bottom) 100%);
    box-shadow: 0 1px 4px rgba(0,0,0,.18);
    overflow: hidden;
  }
  .sheet { top: 22px; width: 261px; height: 338px; }
  .sheet--one { left: 6px; }
  .sheet--two { left: 284px; }
  .sheet--three { left: 558px; }

  .brand {
    position: absolute;
    display: flex;
    align-items: center;
    gap: 5px;
  }
  .brand__dot {
    width: 20px; height: 20px; border-radius: 50%;
    background: var(--brand-red);
    flex: none;
  }
  .brand__name {
    font-weight: 700;
    font-size: 9.5px;
    line-height: 1.15;
    letter-spacing: .2px;
    color: var(--ink);
    text-transform: uppercase;
  }
  .sheet .brand { left: 75px; top: 9px; }

  .suit-row {
    position: absolute;
    left: 27px; top: 150px; width: 210px; height: 40px;
    background: linear-gradient(90deg, var(--suit-faint) 0%, var(--suit-faint) 45%, var(--suit-grey) 55%, var(--suit-grey) 100%);
    opacity: .55;
    border-radius: 4px;
  }

  .small { font-size: 5.2px; line-height: 1.45; color: var(--ink-soft); }
  .red { color: var(--brand-red); font-weight: 700; }

  .footer-line {
    position: absolute; left: 0; right: 0; text-align: center;
    font-size: 5.2px; color: var(--ink-soft); white-space: nowrap;
  }
  .footer-line--a { top: 323px; }
  .footer-line--b { top: 330px; }

  .icon { display: inline-block; width: 4px; height: 4px; border-radius: 50%; background: var(--brand-red); margin: 0 1.5px 0 4px; vertical-align: middle; }

  .contact-list {
    position: absolute; list-style: none;
    font-size: 5.2px; line-height: 1.55; color: var(--ink-soft);
  }
  .contact-list .icon { margin-left: 0; }
  .sheet .contact-list { left: 9px; top: 304px; }

  .tab { position: absolute; width: 5px; border-radius: 0 3px 3px 0; }
  .tab--red { background: var(--brand-red); left: 0; }
  .tab--black { background: var(--tab-black); right: 0; border-radius: 3px 0 0 3px; }
  .sheet .tab { top: 305px; height: 29px; }

  .head-address { position: absolute; left: 194px; top: 12px; }
  .foot-address { position: absolute; right: 9px; top: 313px; text-align: right; }

  .fax-title {
    position: absolute; left: 10px; top: 76px;
    font-family: "Jost", Arial, sans-serif; font-weight: 300;
    font-size: 21px; color: var(--ink);
  }
  .fax-field {
    position: absolute; height: 10px;
    border-bottom: .6px solid var(--rule);
    font-family: "Jost", Arial, sans-serif;
    font-size: 5.2px; color: var(--ink-soft);
  }
  .fax-field--left { left: 9px; width: 135px; }
  .fax-field--right { left: 142px; width: 92px; }
  .fax-checks {
    position: absolute; left: 9px; top: 173px; display: flex; gap: 8px;
    font-family: "Jost", Arial, sans-serif; font-size: 5.2px; color: var(--ink-soft);
  }
  .fax-checks span { display: flex; align-items: center; gap: 3px; }
  .fax-checks i { display: inline-block; width: 6px; height: 6px; border: .6px solid var(--ink-soft); }

  .option-label {
    position: absolute; top: 362px;
    font-family: "Jost", Arial, sans-serif; font-weight: 400;
    font-size: 19px; color: var(--ink-soft);
    transform: translateX(-50%);
  }

  .envelope-back { left: 902px; top: 6px; width: 272px; height: 190px; }
  .envelope-back__flap { position: absolute; left: 0; top: 0; }
  .envelope-back__dot {
    position: absolute; left: 125px; top: 14px;
    width: 22px; height: 22px; border-radius: 50%; background: var(--label);
  }
  .envelope-middle { left: 839px; top: 64px; width: 261px; height: 132px; }
  .envelope-middle__flap { position: absolute; left: 0; top: 0; }
  .envelope-middle__dot {
    position: absolute; left: 131px; top: 13px;
    width: 22px; height: 22px; border-radius: 50%; background: var(--brand-red);
  }
  .envelope { left: 870px; top: 122px; width: 294px; height: 132px; }
  .envelope .brand { left: 8px; top: 10px; }
  .envelope .brand__dot { width: 26px; height: 26px; }
  .envelope .brand__name { font-size: 10.5px; }
  .envelope__address { position: absolute; left: 42px; top: 38px; font-size: 5.6px; line-height: 1.4; color: var(--ink-soft); }
  .envelope__web { position: absolute; left: 42px; top: 122px; font-size: 5.2px; letter-spacing: 1.2px; color: var(--ink-soft); }

  .card { top: 272px; width: 160px; height: 90px; }
  .card--front { left: 862px; }
  .card--back { left: 1035px; }
  .card .brand { left: 8px; top: 7px; }
  .card .brand__dot { width: 22px; height: 22px; }
  .card .brand__name { font-size: 9px; }
  .card .contact-list { left: 8px; top: 47px; font-size: 4.8px; }
  .card .tab { top: 46px; height: 30px; }
  .card .foot-address { right: 9px; top: 56px; font-size: 4.8px; }

  .card__name {
    position: absolute; left: 0; right: 0; top: 13px; text-align: center;
    font-weight: 700; font-size: 12.5px; line-height: 1.25; color: var(--ink);
  }
  .card--back .suit-row { left: 18px; top: 46px; width: 124px; height: 26px; }
  .card__tagline {
    position: absolute; left: 0; right: 0; top: 77px; text-align: center;
    font-weight: 700; font-size: 5.4px; letter-spacing: .4px; color: var(--brand-red);
    white-space: nowrap;
  }
</style>
</head>
<body>

  <section class="sheet sheet--one" aria-label="Letterhead option 1">
    <div class="brand"><span class="brand__dot"></span><p class="brand__name">Corvan<br>Entertainment</p></div>
    <div class="suit-row" role="img" aria-label="Faint row of playing card suit symbols"></div>
    <p class="footer-line footer-line--a"><span class="red">CORVAN LIMITED</span> 18, Lotus Grove Road, Marisvale 20400, Sri Lanka</p>
    <p class="footer-line footer-line--b"><span class="icon"></span>+94 11 2450180 <span class="icon"></span>+94 11 5550100 <span class="icon"></span>info@corvanplay.com <span class="icon"></span>www.corvanplay.com</p>
  </section>

  <section class="sheet sheet--two" aria-label="Letterhead option 2">
    <div class="brand"><span class="brand__dot"></span><p class="brand__name">Corvan<br>Entertainment</p></div>
    <p class="head-address small"><span class="red">CORVAN LIMITED</span><br>18, Lotus Grove Road<br>Marisvale 20400, Sri Lanka</p>
    <span class="tab tab--red"></span>
    <ul class="contact-list">
      <li><span class="icon"></span>+94 11 2450180</li>
      <li><span class="icon"></span>+94 11 5550100</li>
      <li><span class="icon"></span>info@corvanplay.com</li>
      <li><span class="icon"></span>www.corvanplay.com</li>
    </ul>
  </section>

  <section class="sheet sheet--three" aria-label="Fax sheet option 3">
    <div class="brand"><span class="brand__dot"></span><p class="brand__name">Corvan<br>Entertainment</p></div>
    <h1 class="fax-title">FAX</h1>
    <div class="fax-field fax-field--left" style="top:109px">To :</div>
    <div class="fax-field fax-field--right" style="top:109px">From :</div>
    <div class="fax-field fax-field--left" style="top:123px">Fax :</div>
    <div class="fax-field fax-field--right" style="top:123px">Pages :</div>
    <div class="fax-field fax-field--left" style="top:137px">Phone :</div>
    <div class="fax-field fax-field--right" style="top:137px">Date :</div>
    <div class="fax-field fax-field--left" style="top:151px">Re :</div>
    <div class="fax-field fax-field--right" style="top:151px">CC :</div>
    <div class="fax-checks">
      <span><i></i>Urgent</span>
      <span><i></i>For Review</span>
      <span><i></i>Please Comment</span>
      <span><i></i>Please Reply</span>
      <span><i></i>Please Recycle</span>
    </div>
    <span class="tab tab--red"></span>
    <ul class="contact-list">
      <li><span class="icon"></span>+94 11 2450180</li>
      <li><span class="icon"></span>+94 11 5550100</li>
      <li><span class="icon"></span>info@corvanplay.com</li>
      <li><span class="icon"></span>www.corvanplay.com</li>
    </ul>
    <p class="foot-address small"><span class="red">CORVAN LIMITED</span><br>18, Lotus Grove Road<br>Marisvale 20400, Sri Lanka</p>
    <span class="tab tab--black"></span>
  </section>

  <p class="option-label" style="left:130px">Option-1</p>
  <p class="option-label" style="left:406px">Option-2</p>
  <p class="option-label" style="left:680px">Option-3</p>

  <section class="envelope-back" aria-label="Envelope back">
    <svg class="envelope-back__flap" width="272" height="56" viewBox="0 0 272 56">
      <path d="M0 0 H272 V38 Q136 62 0 38 Z" fill="#d42f3a"/>
    </svg>
    <span class="envelope-back__dot"></span>
  </section>

  <section class="envelope-middle" aria-label="Envelope with open flap">
    <svg class="envelope-middle__flap" width="261" height="60" viewBox="0 0 261 60">
      <path d="M0.5 0.5 H260.5 L148 48 Q142 52 130 52 Q118 52 112 48 Z" fill="none" stroke="#444" stroke-width=".8"/>
    </svg>
    <span class="envelope-middle__dot"></span>
  </section>

  <section class="envelope" aria-label="Envelope front">
    <div class="brand"><span class="brand__dot"></span><p class="brand__name">Corvan<br>Entertainment</p></div>
    <p class="envelope__address">18, Lotus Grove Road<br>Marisvale 20400, Sri Lanka</p>
    <p class="envelope__web">www.corvanplay.com</p>
  </section>

  <section class="card card--front" aria-label="Business card front">
    <div class="brand"><span class="brand__dot"></span><p class="brand__name">Corvan<br>Entertainment</p></div>
    <span class="tab tab--red"></span>
    <ul class="contact-list">
      <li><span class="icon"></span>+94 11 2450180</li>
      <li><span class="icon"></span>+94 77 5550100</li>
      <li><span class="icon"></span>+94 11 5550100</li>
      <li><span class="icon"></span>info@corvanplay.com</li>
      <li><span class="icon"></span>www.corvanplay.com</li>
    </ul>
    <p class="foot-address small"><span class="red">CORVAN LIMITED</span><br>18, Lotus Grove Road<br>Marisvale 20400<br>Sri Lanka</p>
    <span class="tab tab--black"></span>
  </section>

  <section class="card card--back" aria-label="Business card back">
    <p class="card__name">CORVAN<br>ENTERTAINMENT</p>
    <div class="suit-row" role="img" aria-label="Row of playing card suit symbols in faint red and grey"></div>
    <p class="card__tagline">THE FINEST TABLES AND THE FAIREST ODDS</p>
  </section>

</body>
</html>
```